Brochure Design - ICT Company

We are an ICT (Information & Communication Technologies) company and need a brochure design. Our main products and services are Office Equipment, Banking Equipment, Software Solutions, IT Hardware, Networking & Communication, Audio Video Solutions and Social Media Marketing. Please check our website www.zolvantek.com for details in our Solutions menu.

Designs should include colors from our website (blue) and our logo (orange/green) in the best possible combination with lighter colors. Graphics and patterns should be sleek and modern. Brochure size to be square shaped (21 cm x 21 cm).

Final design should portray us as a futuristic technology company.

Provide a design with sample images and we can purchase them if required. Alternatively, let us know if the images from our website will suffice.
Updates

Reason: Awaiting more designs and more creativity. If any input is required from us, do inform asap.

Uploaded 2 sample brochure designs that we found interesting - looking for more inspiring ideas.

Thanks

Hi everyone, the following text should appear on the cover of the brochure design:

'Your One Stop Solution Provider for Information & Communication Technologies'

Reason: Awaiting management feedback - might require changes in design. Open to receiving more designs.

Thank you all for participating. Received many creative ideas and will be back with more requests. 

Target Market(s)

Decision Makers in UAE: IT Managers, Purchase Manager, CEO, Finance Managers etc

Industry/Entity Type

Communication

Requirements
Must have
• We have 7 divisions within our company. Brochure should dedicate 2 pages to each company - Text on one side and Image on the other.

7 divisions are: (details on website)
Office Equipment - sales of copiers, fax etc to any industry, any size office
Banking Equipment - sales of coin counters, counterfeit detectors etc to banks and foreign exchange houses
IT & Communication - providing server, email, software licenses to any industry, any size office
Software Solution - Quillbase partner + provide software solution to any industry, any size company
ELV & Security - provide CCTV, security systems to big companies, warehouses etc any industry
AV & Convergence - provide latest technology multi sensory solutions for theatres, opera houses, education sector, hospitality sector, medical sector etc.
Social Media Marketing - provide marketing options to companies through social media (www.zolvanpost.com)

Images to be used in the brochure are attached - they are concept images associated with each division. The design for the inner pages can be created around this basic image.

Cover page - design with logo, 'An Information & Technologies Company'
Back page - Design with address details
Inner sections:
1. About Us
2. Seven divisions as described above

The pattern for the text for inner pages should be:
Heading describing problem
Small Paragraph text describing solution
Small inset images of the

Nice to have
• Modern, sleek look with images that reflect an ICT/IT company - stand out from the regular brochure design
Should not have
• The design should not use old-style design, fonts etc.

```html
<!DOCTYPE html>
<html lang="en">
<head>
<meta charset="utf-8">
<title>Zolvan Technologies – Brochure Spreads</title>
<link href="https://fonts.googleapis.com/css2?family=Arimo:wght@400;700&display=swap" rel="stylesheet">
<style>
:root{
  --navy:#0f2a6b;
  --blue:#1f6fd0;
  --sky:#3aa7e0;
  --cyan:#a9dde3;
  --orange:#f29a1f;
  --green:#9fc83c;
  --red:#e2231a;
  --ink:#333;
  --grey:#4a4a4a;
  --yellow:#ffe500;
}
*{box-sizing:border-box;margin:0;padding:0}
html,body{width:1102px;height:1200px;overflow:hidden;background:#fff;font-family:"Arimo",Arial,sans-serif;color:var(--ink)}
.spread{position:absolute;width:505px;height:255px;overflow:hidden;
  background:linear-gradient(90deg,#fff 0,#f3f3f3 46%,#d8d8d8 50%,#f3f3f3 54%,#fff 100%);
  box-shadow:0 2px 5px rgba(0,0,0,.25)}
.abs{position:absolute}
.photo{position:absolute}
.logo{position:absolute;display:flex;align-items:center;gap:3px}
.logo .mark{width:8px;height:8px;background:var(--orange)}
.logo .name{font-size:5px;font-weight:700;line-height:1.1;color:var(--ink);width:48px}
.body-text{position:absolute;font-size:4px;line-height:1.35;padding:5px}
.pill{position:absolute;border-radius:8px;padding:3px 6px;font-size:10px;line-height:1;text-align:center;color:#111}
.label{position:absolute;font-size:4.5px;font-weight:700}
/* cover */
.cover{background:linear-gradient(100deg,var(--navy) 0,#1b3f94 45%,var(--blue) 100%)}
.cover .name{color:#fff}
.cover-pattern{position:absolute;left:0;top:0;width:505px;height:231px;
  background:radial-gradient(ellipse at 78% 20%,rgba(255,255,255,.10),rgba(255,255,255,0) 45%),
             radial-gradient(ellipse at 55% 80%,rgba(255,255,255,.07),rgba(255,255,255,0) 40%)}
.cover-url{position:absolute;left:442px;top:115px;width:62px;height:10px;background:#fff;font-size:4.5px;padding:3px 4px;color:var(--navy)}
.cover-tag{position:absolute;left:307px;top:127px;font-size:7.5px;color:#fff}
.contact{position:absolute;left:0;bottom:0;width:505px;height:24px;background:rgba(255,255,255,.08)}
.contact .tab{position:absolute;left:8px;top:2px;background:#fff;color:var(--navy);font-size:4px;padding:1px 3px}
.contact .line{position:absolute;top:10px;font-size:3.5px;color:#fff}
.contact .services{position:absolute;left:262px;top:16px;font-size:3.5px;color:#cfe0ff}
/* about */
.about-panel{position:absolute;left:13px;top:50px;width:108px;height:205px;background:var(--cyan)}
.about-panel h2{position:absolute;left:2px;top:4px;font-size:20px;color:var(--blue);font-weight:700}
.list-item{position:absolute;font-size:4.5px;font-weight:700}
.section-title{position:absolute;font-weight:700;white-space:nowrap}
</style>
</head>
<body>

<!-- Cover -->
<section class="spread cover" style="left:40px;top:43px">
  <div class="cover-pattern" role="img" aria-label="Faint circuit and ring pattern on blue background"></div>
  <div class="logo" style="left:100px;top:127px"><span class="mark"></span><span class="name">ZOLVAN TECHNOLOGIES L.L.C.</span></div>
  <div class="logo" style="left:412px;top:19px"><span class="mark"></span><span class="name">ZOLVAN TECHNOLOGIES L.L.C.</span></div>
  <div class="cover-url">www.zolvantek.com</div>
  <div class="cover-tag">An Information &amp; Technologies Company</div>
  <div class="contact">
    <span class="tab">Contact Us</span>
    <span class="line" style="left:10px">Tel 000 0000 Fax 000 0001</span>
    <span class="line" style="left:80px">Tel 000 0000 Fax 000 0001</span>
    <span class="line" style="left:150px">Tel 000 0000 Fax 000 0001</span>
    <span class="line" style="left:440px;top:3px">www.zolvantek.com</span>
    <span class="services">Office Automation | IT &amp; Communications | Software Solutions | ELV &amp; Security | AV &amp; Convergence | Social Media</span>
  </div>
</section>

<!-- About Us / Office Systems -->
<section class="spread" style="left:562px;top:43px">
  <div class="about-panel">
    <h2>About Us</h2>
    <p class="body-text" style="left:0;top:30px;width:108px">Every business faces rising equipment costs. Scattered contracts, mixed suppliers and no standards slow teams down and drain budgets. We bring every office, banking, network and security need under one roof, with one partner, one support line and one clear plan for growth. Our specialists design, supply and maintain solutions that keep your workplace running smoothly every day.</p>
  </div>
  <div class="photo" role="img" aria-label="Sphere made of crumpled paper documents" style="left:138px;top:17px;width:200px;height:200px;border-radius:50%;background:radial-gradient(circle at 40% 35%,#f2f2f2,#9a9a9a 75%,#6e6e6e)"></div>
  <div class="pill" style="left:212px;top:49px;background:#f6e21a">Copier<br>contracts</div>
  <div class="pill" style="left:145px;top:106px;background:var(--orange)">No standardization</div>
  <div class="pill" style="left:262px;top:90px;background:#5cc7d0">Fax service<br>agreements</div>
  <div class="pill" style="left:232px;top:133px;background:#7ec44a">Toner from<br>multiple suppliers</div>
  <div class="pill" style="left:168px;top:165px;background:#3fb7a8">High<br>administration<br>costs</div>
  <div class="logo" style="left:448px;top:14px"><span class="mark"></span><span class="name">ZOLVAN TECHNOLOGIES L.L.C.</span></div>
  <svg class="abs" width="505" height="255" style="left:0;top:0" aria-hidden="true">
    <g stroke="#555" stroke-width=".5" stroke-dasharray="2 1.5" fill="none">
      <line x1="345" y1="90" x2="366" y2="40"/><line x1="345" y1="90" x2="403" y2="57"/>
      <line x1="345" y1="90" x2="418" y2="74"/><line x1="345" y1="90" x2="428" y2="95"/>
      <line x1="345" y1="90" x2="420" y2="112"/><line x1="345" y1="90" x2="393" y2="130"/>
    </g>
  </svg>
  <span class="list-item" style="left:368px;top:36px">Copy Systems</span>
  <span class="list-item" style="left:405px;top:53px">Print Systems</span>
  <span class="list-item" style="left:420px;top:70px">Large Format Systems</span>
  <span class="list-item" style="left:430px;top:91px">FAX Machines</span>
  <span class="list-item" style="left:422px;top:108px">Shredding Machines</span>
  <span class="list-item" style="left:395px;top:126px">Baling Machines</span>
  <span class="section-title" style="left:398px;top:160px;font-size:10px;color:#e8551a">Office Systems</span>
  <p class="body-text" style="left:363px;top:178px;width:133px;height:77px;background:var(--green)">We are a leading supplier of office automation systems, from copiers and printers to fax and shredding machines. One managed contract cuts costs, simplifies service and lifts the productivity of every department.</p>
</section>

<!-- Banking Equipment -->
<section class="spread" style="left:40px;top:325px">
  <div class="photo" role="img" aria-label="Teal banknote counting and sorting machine" style="left:20px;top:20px;width:225px;height:200px;background:linear-gradient(160deg,#cfe3e3,#5e9ea0 60%,#e9eeee)"></div>
  <div class="abs" style="left:250px;top:53px;width:255px;height:30px;background:var(--orange)">
    <span class="section-title" style="left:27px;top:3px;font-size:16px;color:#fff">BANKING EQUIPMENT</span>
    <span class="abs" style="left:27px;top:22px;font-size:4px;color:#fff">•Currency Counter &amp; Sorter •Coin Counter &amp; Sorter •Counterfeit Currency Detector</span>
  </div>
  <svg class="abs" width="505" height="255" style="left:0;top:0" aria-hidden="true">
    <g stroke="var(--orange)" stroke-width=".6" stroke-dasharray="3 2" fill="none">
      <path d="M230 20 Q330 10 420 53"/><path d="M250 230 Q330 250 392 220"/>
      <line x1="380" y1="83" x2="380" y2="157"/>
    </g>
  </svg>
  <p class="body-text" style="left:392px;top:157px;width:88px;height:90px;border:.7px dashed var(--orange)">Our banking equipment covers currency counters, coin sorters and counterfeit detectors built for banks and exchange houses. Each machine is fast, accurate and easy to use, helping tellers process cash securely and keeping every transaction in line with current regulations.</p>
  <div class="logo" style="left:448px;top:15px"><span class="mark"></span><span class="name">ZOLVAN TECHNOLOGIES L.L.C.</span></div>
</section>

<!-- ELV & Security -->
<section class="spread" style="left:562px;top:325px">
  <div class="abs" style="left:35px;top:42px;width:170px;height:18px;background:#111;transform:rotate(-4deg)">
    <span class="section-title" style="left:12px;top:3px;font-size:11px;color:var(--yellow)">ELV &amp; Security Systems</span>
  </div>
  <div class="photo" role="img" aria-label="Security camera silhouette against a grey brick wall" style="left:18px;top:70px;width:225px;height:170px;background:linear-gradient(135deg,#d9d9d9,#8c8c8c 55%,#2a2a2a)"></div>
  <div class="photo" role="img" aria-label="Small grey fingerprint on a card" style="left:331px;top:90px;width:32px;height:55px;background:#d0d0d0"></div>
  <div class="photo" role="img" aria-label="Large orange fingerprint" style="left:386px;top:75px;width:82px;height:80px;background:linear-gradient(135deg,#f7c57a,#f2a640)"></div>
  <svg class="abs" width="505" height="255" style="left:0;top:0" aria-hidden="true">
    <g stroke="#222" stroke-width=".6" fill="none">
      <line x1="395" y1="42" x2="450" y2="92"/><line x1="360" y1="54" x2="420" y2="105"/>
      <line x1="355" y1="66" x2="398" y2="120"/>
      <circle cx="450" cy="92" r="4" stroke-width="1.2"/><circle cx="420" cy="105" r="4" stroke-width="1.2"/><circle cx="398" cy="120" r="4" stroke-width="1.2"/>
    </g>
  </svg>
  <span class="label" style="left:377px;top:37px">Garage Doors</span>
  <span class="label" style="left:327px;top:49px">Access Control</span>
  <span class="label" style="left:345px;top:61px">CCTV</span>
  <p class="body-text" style="left:356px;top:180px;width:112px;height:75px;background:var(--grey);color:#eee">Our security services suit projects of every scale, from warehouses to corporate towers. We offer CCTV, access control, intrusion alarms, gate barriers, guard tours and fire detection, all designed, installed and maintained by one certified team.</p>
  <div class="logo" style="left:448px;top:15px"><span class="mark"></span><span class="name">ZOLVAN TECHNOLOGIES L.L.C.</span></div>
</section>

<!-- IT & Communications -->
<section class="spread" style="left:40px;top:607px">
  <div class="abs" style="left:0;top:33px;width:200px;height:25px;background:#2b8fd6;transform:rotate(-2deg)">
    <span class="section-title" style="left:18px;top:6px;font-size:14px;color:#fff">IT &amp; COMMUNICATIONS</span>
  </div>
  <div class="photo" role="img" aria-label="Bundle of coloured network cables with plugs" style="left:85px;top:73px;width:125px;height:182px;background:linear-gradient(160deg,#7ec44a,#2b8fd6 45%,#e2231a 75%,#f2d21a)"></div>
  <span class="label" style="left:215px;top:95px;color:var(--orange);font-weight:400">Server Solutions</span>
  <span class="label" style="left:218px;top:108px;color:var(--orange);font-weight:400">Email Solutions</span>
  <span class="label" style="left:220px;top:121px;color:var(--orange);font-weight:400">Software Licensing</span>
  <span class="label" style="left:222px;top:134px;color:var(--orange);font-weight:400">Storage Solutions</span>
  <span class="label" style="left:224px;top:147px;color:var(--orange);font-weight:400">Data Centre Services</span>
  <p class="body-text" style="left:293px;top:108px;width:97px;height:147px;background:#a7c83a">The IT landscape changes every day. Our team supplies servers, storage, email systems and software licences that grow with your business. We plan, install and support the full infrastructure so your staff stay connected, your data stays safe and your costs stay under control.</p>
  <div class="photo" role="img" aria-label="Row of dark server racks" style="left:380px;top:183px;width:100px;height:72px;background:linear-gradient(180deg,#6b7380,#1d2026)"></div>
  <span class="label" style="left:410px;top:44px;font-weight:400">Data · Networking</span>
  <p class="body-text" style="left:403px;top:52px;width:95px">Good network design brings speed, reliability and security to every office. We build wired and wireless networks, structured cabling and secure remote links, then monitor them closely so that voice, video and data flow without interruption across all your sites.</p>
  <div class="logo" style="left:448px;top:15px"><span class="mark"></span><span class="name">ZOLVAN TECHNOLOGIES L.L.C.</span></div>
</section>

<!-- AV & Convergence -->
<section class="spread" style="left:562px;top:607px">
  <div class="abs" style="left:33px;top:25px;width:52px;height:35px;background:#1f72c9"><span class="section-title" style="left:6px;top:2px;font-size:28px;color:#fff">AV</span></div>
  <span class="section-title" style="left:89px;top:32px;font-size:18px;color:#1f72c9">&amp;</span>
  <div class="abs" style="left:113px;top:35px;width:135px;height:20px;background:#2a8ad9"><span class="section-title" style="left:5px;top:3px;font-size:13px;color:#fff">Convergence</span></div>
  <div class="photo" role="img" aria-label="Video wall of tilted screens showing a concert scene" style="left:3px;top:62px;width:225px;height:183px;background:linear-gradient(135deg,#7fb6e6,#3b5d8f 50%,#f0d2a8)"></div>
  <div class="abs" style="left:288px;top:13px;width:110px;height:110px;border-radius:50%;background:#a5dde6"></div>
  <div class="abs" style="left:303px;top:38px;font-size:4.3px;line-height:1.45">
    ▪ Board Room Solutions<br>▪ Professional Audio &amp; Lighting<br>▪ Background Music &amp; Public<br>&nbsp;&nbsp;Address System<br>▪ Information Displays &amp; Kiosks<br>▪ Audio &amp; Video Conferencing<br>▪ Educational Presentation Equipments
  </div>
  <div class="photo" role="img" aria-label="White 3D figures holding display panels" style="left:283px;top:118px;width:95px;height:75px;background:linear-gradient(180deg,#f4f4f4,#cfd6dc)"></div>
  <p class="body-text" style="left:406px;top:113px;width:88px;height:142px;background:#45aee3;color:#fff">We design and install complete audio visual systems for theatres, schools, hotels and hospitals. From boardroom displays to concert sound, our engineers blend lighting, video and control into one simple experience that engages every audience and is easy for staff to run.</p>
  <div class="logo" style="left:448px;top:15px"><span class="mark"></span><span class="name">ZOLVAN TECHNOLOGIES L.L.C.</span></div>
</section>

<!-- Software Solution -->
<section class="spread" style="left:40px;top:890px">
  <span class="section-title" style="left:45px;top:38px;font-size:17px;color:var(--red);font-weight:400">Software<b>Solution</b></span>
  <div class="photo" role="img" aria-label="White puzzle pieces with one red piece lifted" style="left:20px;top:98px;width:210px;height:95px;background:linear-gradient(180deg,#f4f4f4,#c8c8c8)"></div>
  <div class="abs" style="left:305px;top:0;width:88px;height:255px;background:var(--sky)"></div>
  <svg class="abs" width="505" height="255" style="left:0;top:0" aria-hidden="true">
    <circle cx="348" cy="85" r="43" fill="var(--red)" stroke="#fff" stroke-width="2"/>
    <g stroke="#fff" stroke-width="2">
      <line x1="348" y1="85" x2="348" y2="42"/><line x1="348" y1="85" x2="391" y2="85"/><line x1="348" y1="85" x2="318" y2="116"/>
    </g>
    <g fill="#fff" font-family="Arimo, Arial, sans-serif" font-size="4.5">
      <text x="360" y="68">Consulting</text>
      <text x="322" y="80">Enterprise</text><text x="322" y="86">Solutions</text>
      <text x="352" y="106">IT Services</text>
    </g>
  </svg>
  <p class="body-text" style="left:307px;top:140px;width:86px;color:#fff">As a Quillbase partner we deliver enterprise software that fits the way you work. Our consultants map your processes, configure each module and train your people, giving you clear reports, faster decisions and systems that scale with your company.</p>
  <div class="logo" style="left:448px;top:15px"><span class="mark"></span><span class="name">ZOLVAN TECHNOLOGIES L.L.C.</span></div>
</section>

<!-- Social Media Marketing -->
<section class="spread" style="left:562px;top:890px">
  <span class="section-title" style="left:30px;top:25px;font-size:8px">Social Media Marketing</span>
  <div class="photo" role="img" aria-label="Colourful network of people figures with speech bubbles" style="left:15px;top:48px;width:330px;height:175px;background:linear-gradient(120deg,#8fd14f,#4aa9e0 35%,#f29a1f 65%,#e2231a)"></div>
  <p class="body-text" style="left:406px;top:118px;width:90px;height:137px;background:#45aee3;color:#fff">Reach your customers where they spend their time. Through www.zolvanpost.com we plan campaigns, create content and manage communities across social channels, then measure every result so your brand grows with each post.</p>
  <div class="logo" style="left:448px;top:15px"><span class="mark"></span><span class="name">ZOLVAN TECHNOLOGIES L.L.C.</span></div>
</section>

</body>
</html>
```